Website for "Bright Morrow Ltd" cleaning bsuiness

We require a website to expose our business to the local market. We want to provide background on who we are and what we do but in an easily digestible way. We clean domestic and commercial premises and want to provide a list of all of our services to potential customers. We operate out of Warrington in the UK.

We would like the website to be animated in some way so that the experience of using it is not dull or mundane. This website needs to be an extension of our company.

Target Market(s)

30 - 60 year olds for Domestic plus commercial clients

Industry/Entity Type

Cleaning Service

Coding

Coded - Design and coding required

Number of Pages Required

4 page

Font styles to use
Sans Serif

Colors
0455a3
3176b5
85acd3
cfdeed
ffffff
000000
1b1b1b
c8c8c8
757575

Requirements
Must have
• Logo which has been provided. Theme based around the logo and its colours. Simple layout to avoid confusion.
Nice to have
• Animations where possible to impress the customer.
Should not have
• any pictures of cleaning equipment, fairies, maids etc

```html
<!DOCTYPE html>
<html lang="en">
<head>
<meta charset="utf-8">
<title>Bright Morrow Ltd – Blog</title>
<link rel="stylesheet" href="https://fonts.googleapis.com/css2?family=Raleway:wght@400;500;600;700&family=Arimo:wght@400;700&display=swap">
<style>
:root{
  --blue:#0455a3;
  --blue-mid:#3176b5;
  --blue-light:#85acd3;
  --blue-pale:#cfdeed;
  --white:#ffffff;
  --ink:#1b1b1b;
  --grey:#757575;
  --grey-line:#c8c8c8;
}
*{margin:0;padding:0;box-sizing:border-box}
html,body{width:707px;height:1200px;overflow:hidden;background:var(--white)}
body{position:relative;font-family:'Arimo',Arial,sans-serif;color:var(--grey)}
.abs{position:absolute}
h1,h2,h3{font-weight:400}

/* hero */
.hero-photo{left:0;top:0;width:707px;height:402px;
  background:linear-gradient(100deg,#e9ecef 0%,#f7f7f7 35%,#eef2f6 60%,#c9d8e6 100%)}
.hero-shape{left:0;top:0}
.nav{top:0;left:0;width:707px;height:47px;border-bottom:1px solid var(--grey-line)}
.nav a{position:absolute;top:18px;font-size:10.5px;color:var(--ink);text-decoration:none;letter-spacing:.2px;white-space:nowrap}
.nav a.active{color:var(--blue)}
.nav .active-bar{position:absolute;left:199px;top:44px;width:46px;height:2px;background:var(--blue)}
.brand{left:0;width:707px;top:180px;text-align:center;font-family:'Raleway',sans-serif;font-weight:700;font-size:40px;color:var(--blue);line-height:1;white-space:nowrap}
.brand .dot{display:inline-block;width:18px;height:18px;border-radius:50%;background:var(--blue);margin-right:10px;vertical-align:middle}

/* blog */
.section-title{top:418px;left:0;width:707px;text-align:center;font-family:'Raleway',sans-serif;font-weight:400;font-size:24px;color:var(--blue);letter-spacing:.5px}
.post-title{font-family:'Raleway',sans-serif;font-weight:400;color:var(--blue)}
.post-main .post-title{left:46px;top:459px;width:400px;font-size:17px;line-height:21px}
.date{font-size:8.5px;color:var(--grey);display:flex;align-items:center;gap:4px;white-space:nowrap}
.date svg{width:8px;height:8px}
.photo{background:linear-gradient(135deg,#c9b9a4,#e6dfd6 50%,#b98e63)}
.body-text{font-size:8px;line-height:16px;color:var(--grey)}
.card .post-title{font-size:9.5px;line-height:14.5px;width:190px}
.card .body-text{font-size:7.8px;line-height:15px;width:190px}
.more{color:var(--blue);font-weight:700;text-decoration:none}

/* footer */
.footer-bg{left:0;top:955px;width:707px;height:212px}
.footer h3{position:absolute;font-family:'Raleway',sans-serif;font-weight:700;font-size:11px;color:var(--blue);letter-spacing:.3px;white-space:nowrap}
.links{width:110px}
.links li{list-style:none;position:absolute;left:0;font-size:8.5px;color:var(--ink);padding-left:12px;white-space:nowrap;line-height:10px}
.links li::before{content:"";position:absolute;left:0;top:3px;width:4px;height:4px;border:1px solid var(--blue)}
.links li.current::before{background:var(--blue)}
.contact{font-size:8.5px;color:var(--ink);line-height:16px}
.contact.nowrap{white-space:nowrap}
.contact svg{position:absolute;left:0;width:13px;height:13px}
.footer-brand{left:46px;top:1062px;font-family:'Raleway',sans-serif;font-weight:700;font-size:14px;color:var(--blue);line-height:1.1;white-space:nowrap}
.footer-brand .dot{display:inline-block;width:9px;height:9px;border-radius:50%;background:var(--blue);margin-right:5px}
.email-input{left:514px;top:1092px;width:148px;height:24px;border:1px solid var(--grey-line);background:var(--white);font-size:8.5px;color:var(--ink);padding:7px 6px}
.submit{left:514px;top:1122px;width:92px;height:24px;background:var(--blue);color:var(--white);font-size:11px;text-align:center;line-height:24px}
.bottom-bar{left:0;top:1166px;width:707px;height:34px;background:var(--blue);color:var(--blue-pale);font-size:8.5px;text-align:center;line-height:34px}
.bottom-bar b{color:var(--white)}
</style>
</head>
<body>

<header>
  <div class="abs hero-photo" role="img" aria-label="Bright, clean white living room and office interior"></div>
  <svg class="abs hero-shape" width="707" height="420" viewBox="0 0 707 420" aria-hidden="true">
    <defs>
      <linearGradient id="edge" x1="0" x2="1">
        <stop offset="0" stop-color="#0455a3"/>
        <stop offset=".55" stop-color="#0455a3"/>
        <stop offset="1" stop-color="#85acd3"/>
      </linearGradient>
    </defs>
    <polygon points="0,402 354,338 707,402 707,420 0,420" fill="#ffffff"/>
    <polyline points="0,400 354,338 707,400" fill="none" stroke="url(#edge)" stroke-width="5"/>
  </svg>
  <nav class="abs nav">
    <a class="active" href="#" style="left:207px">HOME</a>
    <a href="#" style="left:277px">ABOUT US</a>
    <a href="#" style="left:356px">SERVICES</a>
    <a href="#" style="left:435px">BLOG</a>
    <a href="#" style="left:489px">CONTACT US</a>
    <span class="active-bar"></span>
  </nav>
  <div class="abs brand"><span class="dot"></span>Bright Morrow Ltd</div>
</header>

<main>
  <h1 class="abs section-title">BLOG</h1>

  <article class="post-main">
    <h2 class="abs post-title">Lorem Ipsum is simply dummy text of the printing and typesetting industry.</h2>
    <div class="abs date" style="left:46px;top:508px">
      <svg viewBox="0 0 10 10"><rect x=".5" y="1.5" width="9" height="8" fill="none" stroke="#757575"/><line x1=".5" y1="4" x2="9.5" y2="4" stroke="#757575"/></svg>07 November 2016
    </div>
    <div class="abs photo" style="left:46px;top:526px;width:405px;height:203px" role="img" aria-label="Hand holding a house key in front of a room with moving boxes"></div>
    <p class="abs body-text" style="left:46px;top:743px;width:405px">Lorem Ipsum is simply dummy text of the printing and typesetting industry. Lorem Ipsum has been the industry's standard dummy text ever since the 1500s, when an unknown printer took a galley of type and scrambled it to make a type specimen book.It has survived not only five centuries. Lorem Ipsum is simply dummy text of the printing and typesetting industry.</p>
    <p class="abs body-text" style="left:46px;top:823px;width:405px">Lorem Ipsum is simply dummy text of the printing and typesetting industry. Lorem Ipsum has been the industry's standard dummy text ever since the 1500s, when an unknown printer took a galley of type and scrambled it to make a type specimen book.It has survived not only five centuries. Lorem Ipsum is simply dummy text of the printing and typesetting industry.Lorem Ipsum is simply dummy text of the printing and typesetting industry. Lorem Ipsum has been the industry's standard dummy text ever since the 1500.</p>
  </article>

  <aside>
    <article class="card">
      <div class="abs photo" style="left:471px;top:462px;width:190px;height:116px;background:linear-gradient(135deg,#dfe6ee,#b9c9da 60%,#e9a05a)" role="img" aria-label="Person wiping a window with a cloth"></div>
      <h3 class="abs post-title" style="left:472px;top:584px">Lorem Ipsum is simply dummy text of the printing and typesetting industry.</h3>
      <div class="abs date" style="left:472px;top:618px">
        <svg viewBox="0 0 10 10"><rect x=".5" y="1.5" width="9" height="8" fill="none" stroke="#757575"/><line x1=".5" y1="4" x2="9.5" y2="4" stroke="#757575"/></svg>07 November 2016
      </div>
      <p class="abs body-text" style="left:472px;top:629px">Lorem Ipsum is simply dummy text of the printing and typesetting industry. Lorem Ipsum has been the industry's standard dummy <a class="more" href="#">READ MORE</a></p>
    </article>
    <article class="card">
      <div class="abs photo" style="left:471px;top:701px;width:190px;height:116px;background:linear-gradient(135deg,#eef1f4,#cfdeed 55%,#8aa9c9)" role="img" aria-label="Cleaning team at work in a bright corridor"></div>
      <h3 class="abs post-title" style="left:472px;top:823px">Lorem Ipsum is simply dummy text of the printing and typesetting industry.</h3>
      <div class="abs date" style="left:472px;top:857px">
        <svg viewBox="0 0 10 10"><rect x=".5" y="1.5" width="9" height="8" fill="none" stroke="#757575"/><line x1=".5" y1="4" x2="9.5" y2="4" stroke="#757575"/></svg>07 November 2016
      </div>
      <p class="abs body-text" style="left:472px;top:868px">Lorem Ipsum is simply dummy text of the printing and typesetting industry. Lorem Ipsum has been the industry's standard dummy <a class="more" href="#">READ MORE</a></p>
    </article>
  </aside>
</main>

<footer class="footer">
  <svg class="abs footer-bg" width="707" height="212" viewBox="0 0 707 212" role="img" aria-label="Soft, faded photo of a smiling person resting on a white rug">
    <defs>
      <linearGradient id="fade" x1="0" x2="1">
        <stop offset="0" stop-color="#f3ece6"/>
        <stop offset=".3" stop-color="#f7f3ef"/>
        <stop offset="1" stop-color="#fbfaf9"/>
      </linearGradient>
    </defs>
    <polygon points="0,65 354,3 707,67 707,212 0,212" fill="url(#fade)"/>
    <polyline points="0,65 354,3 707,67" fill="none" stroke="#0455a3" stroke-width="5"/>
  </svg>

  <div class="abs footer-brand"><span class="dot"></span>Bright Morrow Ltd</div>

  <h3 style="left:208px;top:1026px">USEFULL LINKS</h3>
  <ul class="abs links" style="left:207px;top:0">
    <li class="current" style="top:1050px">Home</li>
    <li style="top:1066px">About Us</li>
    <li style="top:1082px">Services</li>
    <li style="top:1098px">Blog</li>
    <li style="top:1114px">Contact Us</li>
  </ul>

  <h3 style="left:358px;top:1026px">GET IN TOUCH</h3>
  <div class="abs contact" style="left:356px;top:1048px;width:140px;padding-left:25px">
    <svg viewBox="0 0 14 14" style="top:3px"><polygon points="1,3 5,1.5 9,3 13,1.5 13,11 9,12.5 5,11 1,12.5" fill="none" stroke="#0455a3"/><line x1="5" y1="1.5" x2="5" y2="11" stroke="#0455a3"/><line x1="9" y1="3" x2="9" y2="12.5" stroke="#0455a3"/></svg>
    101- Lorem ipsum is simple dummy text of print and type setting industry
  </div>
  <div class="abs contact nowrap" style="left:356px;top:1102px;padding-left:25px">
    <svg viewBox="0 0 14 14" style="top:1px"><path d="M3 1.5 L5.5 4 L4.2 5.8 C5 7.7 6.4 9 8.2 9.8 L10 8.5 L12.5 11 L11 12.5 C6 12 2 8 1.5 3 Z" fill="none" stroke="#0455a3"/></svg>
    0700 555 0148
  </div>
  <div class="abs contact nowrap" style="left:356px;top:1125px;padding-left:25px">
    <svg viewBox="0 0 14 14" style="top:2px"><rect x="1" y="3" width="12" height="8.5" fill="none" stroke="#0455a3"/><polyline points="1,3 7,8 13,3" fill="none" stroke="#0455a3"/></svg>
    info@brightmorrowltd.com
  </div>

  <h3 style="left:516px;top:1026px">NEWSLETTER</h3>
  <p class="abs contact" style="left:516px;top:1048px;width:150px;line-height:13.5px">Would you like to receive exclusive access to articles, white papers and our regular monthly newsletter?</p>
  <div class="abs email-input">Enter Email Id</div>
  <div class="abs submit">SUBMIT</div>

  <div class="abs bottom-bar">© 2016 <b>Bright Morrow -</b>&nbsp; All rights reserved.</div>
</footer>

</body>
</html>
```